Business card for medical clinic

I need an upmarket, modern medical/health business card for my clinic

Contact Information for Business Card

name, address, email, qr code

```html
<!DOCTYPE html>
<html lang="en">
<head>
<meta charset="utf-8">
<title>Meridian Care Group — Business Card</title>
<link rel="stylesheet" href="https://fonts.googleapis.com/css2?family=Montserrat:wght@400;500;600;800&display=swap">
<style>
  :root {
    --backdrop: #6e6e70;
    --paper: #ffffff;
    --navy: #1e2944;
    --navy-deep: #172038;
    --accent: #1ea0e0;
    --ink: #4a4d55;
    --name-ink: #1f3560;
    --emboss: #8fb2df;
  }
  * { box-sizing: border-box; margin: 0; padding: 0; }
  html, body { width: 1200px; height: 800px; overflow: hidden; }
  body {
    background: var(--backdrop);
    font-family: "Montserrat", sans-serif;
    display: flex;
    flex-direction: column;
    align-items: center;
    justify-content: center;
    gap: 56px;
  }
  .card {
    position: relative;
    width: 560px;
    height: 320px;
    border-radius: 22px;
    box-shadow: 0 0 0 3px var(--accent), 0 18px 30px rgba(0,0,0,0.35);
    overflow: hidden;
  }
  .card--front { background: var(--paper); }
  .card--back { background: linear-gradient(160deg, var(--navy) 0%, var(--navy-deep) 100%); }

  .brand {
    position: absolute;
    display: flex;
    align-items: center;
    gap: 12px;
  }
  .brand__mark {
    border-radius: 50%;
    border: 3px solid var(--accent);
    flex: none;
  }
  .brand__name {
    font-weight: 600;
    text-transform: uppercase;
    letter-spacing: 0.06em;
    line-height: 1.2;
    white-space: nowrap;
  }
  .card--front .brand { left: 42px; top: 76px; max-width: 230px; }
  .card--front .brand__mark { width: 54px; height: 54px; }
  .card--front .brand__name { font-size: 16px; color: var(--name-ink); }

  .holder { position: absolute; right: 40px; top: 46px; text-align: right; }
  .holder__name { font-weight: 800; font-size: 22px; color: var(--name-ink); letter-spacing: 0.01em; white-space: nowrap; }
  .holder__role { font-size: 14px; color: var(--ink); margin-top: 2px; }

  .divider {
    position: absolute;
    left: 40px; right: 40px; top: 178px;
    height: 1.5px;
    background: var(--accent);
  }

  .contacts {
    position: absolute;
    left: 40px; top: 196px;
    list-style: none;
    display: flex;
    flex-direction: column;
    gap: 9px;
  }
  .contacts li { display: flex; align-items: center; gap: 10px; font-size: 14px; color: var(--ink); }
  .contacts svg { width: 16px; height: 16px; flex: none; }

  .address {
    position: absolute;
    right: 40px; top: 198px;
    text-align: right;
    font-style: normal;
    font-size: 14px;
    line-height: 1.6;
    color: var(--ink);
  }

  .card--back .brand { left: 50%; top: 50%; transform: translate(-50%, -50%); gap: 18px; }
  .card--back .brand__mark { width: 90px; height: 90px; border-color: var(--emboss); opacity: 0.55; }
  .card--back .brand__name { font-size: 30px; color: var(--emboss); }
</style>
</head>
<body>

  <section class="card card--front" aria-label="Business card front">
    <div class="brand">
      <span class="brand__mark"></span>
      <span class="brand__name">Meridian Care<br>Group</span>
    </div>

    <div class="holder">
      <div class="holder__name">DANIEL HARLOW</div>
      <div class="holder__role">President</div>
    </div>

    <div class="divider"></div>

    <ul class="contacts">
      <li>
        <svg viewBox="0 0 16 16"><circle cx="8" cy="8" r="8" fill="#1ea0e0"/><path d="M5.3 4.2l1.3 1.6-.7.9c.5 1.1 1.3 1.9 2.4 2.4l.9-.7 1.6 1.3-.8 1.3c-2.8-.3-5.1-2.6-5.4-5.4z" fill="#fff"/></svg>
        555-014-2870
      </li>
      <li>
        <svg viewBox="0 0 16 16"><circle cx="8" cy="8" r="8" fill="#1ea0e0"/><rect x="4" y="5.2" width="8" height="5.6" rx="0.6" fill="#fff"/><path d="M4.2 5.5L8 8.4l3.8-2.9" stroke="#1ea0e0" stroke-width="0.9" fill="none"/></svg>
        daniel@meridiancare.com
      </li>
      <li>
        <svg viewBox="0 0 16 16"><circle cx="8" cy="8" r="8" fill="#1ea0e0"/><circle cx="8" cy="8" r="4" stroke="#fff" stroke-width="1" fill="none"/><ellipse cx="8" cy="8" rx="1.7" ry="4" stroke="#fff" stroke-width="0.9" fill="none"/><path d="M4 8h8" stroke="#fff" stroke-width="0.9"/></svg>
        www.meridiancare.com
      </li>
    </ul>

    <address class="address">
      4518 Coastline Drive<br>
      Bayview CA 94012
    </address>
  </section>

  <section class="card card--back" aria-label="Business card back">
    <div class="brand">
      <span class="brand__mark"></span>
      <span class="brand__name">Meridian Care<br>Group</span>
    </div>
  </section>

</body>
</html>
```